Weightloss company needs Business Card

We want a business card that is clean and professional, yet portrays that we are a friendly, innovative, and versatile program designed to fit the needs of our clients.
I would like there to be 2 sides, one side having an appointment card, and the other side containing the logo and business information. There can be decorations on both sides. The logo is attached.

Target Market(s)

Men and women 40-60

Industry/Entity Type

Business

Contact Information for Business Card

Font styles to use
Sans Serif

Requirements
Must have
• The logo, space for business information
Nice to have
• The colors in the logo
Should not have
• No pictures of people or food

```html
<!DOCTYPE html>
<html lang="en">
<head>
<meta charset="utf-8">
<title>Renewal Wellness – Business Card</title>
<link href="https://fonts.googleapis.com/css2?family=Open+Sans:ital,wght@0,400;0,600;0,700;1,400&display=swap" rel="stylesheet">
<style>
  :root {
    --pink: #e8275a;
    --cyan: #35c6e8;
    --ink: #4a4a4a;
    --muted: #8a8a8a;
    --line: #bdbdbd;
    --card: #ffffff;
    --bg: #e9e6e1;
  }
  * { box-sizing: border-box; margin: 0; padding: 0; }
  html, body { width: 1200px; height: 950px; overflow: hidden; }
  body {
    background: var(--bg);
    font-family: "Open Sans", Arial, sans-serif;
    color: var(--ink);
    position: relative;
  }
  .card {
    position: absolute;
    left: 250px;
    width: 700px;
    height: 400px;
    background: var(--card);
    border-radius: 22px;
    box-shadow: 0 6px 18px rgba(0,0,0,.18);
    overflow: hidden;
  }
  .card--front { top: 55px; }
  .card--back { top: 495px; }

  /* Front */
  .brand {
    position: absolute;
    left: 60px; top: 62px;
    display: flex; align-items: center; gap: 14px;
  }
  .brand__dot { width: 22px; height: 22px; border-radius: 50%; background: var(--cyan); }
  .brand__name { font-size: 40px; font-weight: 700; color: var(--pink); letter-spacing: -.5px; }

  .person { position: absolute; left: 60px; bottom: 50px; }
  .person__name { font-size: 24px; color: var(--pink); letter-spacing: .5px; }
  .person__title { font-size: 17px; color: var(--cyan); margin-bottom: 12px; }
  .contact { list-style: none; font-size: 17px; color: var(--ink); }
  .contact li { display: flex; align-items: center; gap: 10px; line-height: 28px; }
  .contact svg { width: 16px; height: 16px; flex: none; }

  .divider {
    position: absolute; left: 372px; bottom: 50px;
    width: 1px; height: 150px; background: var(--line);
  }
  .address {
    position: absolute; left: 398px; bottom: 58px;
    font-size: 17px; line-height: 28px; color: var(--ink); font-style: normal;
  }

  /* Back */
  .appt__heading {
    position: absolute; right: 60px; top: 48px;
    font-size: 30px; font-weight: 700; color: var(--pink);
  }
  .appt__row {
    position: absolute; left: 60px; right: 60px;
    display: flex; align-items: flex-end; gap: 12px;
    font-size: 18px;
  }
  .appt__row--who { top: 125px; }
  .appt__row--time { top: 190px; }
  .fill { flex: 1; border-bottom: 2px dotted var(--line); height: 22px; }
  .label-pink { color: var(--pink); }
  .ampm { color: var(--pink); font-size: 14px; }
  .days {
    position: absolute; left: 60px; right: 60px; top: 262px;
    display: flex; justify-content: space-between; list-style: none;
    font-size: 18px; color: var(--pink);
  }
  .days li { display: flex; align-items: center; gap: 8px; }
  .box { width: 17px; height: 17px; border: 1.5px solid var(--ink); }
  .note {
    position: absolute; left: 60px; right: 60px; bottom: 36px;
    font-size: 14px; font-style: italic; color: var(--ink); line-height: 20px;
  }
</style>
</head>
<body>

<section class="card card--front" aria-label="Business card front">
  <div class="brand">
    <span class="brand__dot"></span>
    <span class="brand__name">Renewal Wellness</span>
  </div>

  <div class="person">
    <p class="person__name">MARA ELLISON</p>
    <p class="person__title">CEO/FOUNDER</p>
    <ul class="contact">
      <li>
        <svg viewBox="0 0 16 16"><path fill="var(--pink)" d="M3.5 1.5l2.5 3-1.5 1.5c.8 2 2.5 3.7 4.5 4.5L10.5 9l3 2.5-1.5 2.5C6.5 13.5 2.5 9.5 1.5 4z"/></svg>
        555 210 4471
      </li>
      <li>
        <svg viewBox="0 0 16 16"><rect x="2" y="2" width="12" height="12" fill="none" stroke="var(--pink)" stroke-width="1.6"/></svg>
        555 318 2290
      </li>
      <li>
        <svg viewBox="0 0 16 16"><rect x="1" y="1" width="14" height="14" fill="var(--pink)"/><path d="M3.5 5.5l4.5 3.5 4.5-3.5" fill="none" stroke="#fff" stroke-width="1.3"/></svg>
        mara@renewalwell.com
      </li>
    </ul>
  </div>

  <div class="divider"></div>

  <address class="address">
    412 Alder Street<br>
    Juneau, Alaska 99801<br>
    www.renewalwell.com
  </address>
</section>

<section class="card card--back" aria-label="Appointment card">
  <h2 class="appt__heading">Next Appointment</h2>

  <div class="appt__row appt__row--who">
    <span class="fill"></span>
    <span>has an appointment</span>
  </div>

  <div class="appt__row appt__row--time">
    <span class="label-pink">Time :</span>
    <span class="fill"></span>
    <span class="ampm">AM/PM</span>
  </div>

  <ul class="days">
    <li>Mon <span class="box"></span></li>
    <li>Tue <span class="box"></span></li>
    <li>Wed <span class="box"></span></li>
    <li>Thu <span class="box"></span></li>
    <li>Fri <span class="box"></span></li>
    <li>Sat <span class="box"></span></li>
  </ul>

  <p class="note">Please give 24 hours notice if you are unable to keep your appointment or<br>a cancellation fee may be charged.</p>
</section>

</body>
</html>
```